Working Capital graphics

Our business advisory firm requires 9 images to be re-created and improved in the branding of our business.

The 9 images have been uploaded below and the colours and branding of the business can be found at the website www.tallowmereadvisory.com.au

```html
<!DOCTYPE html>
<html lang="en">
<head>
<meta charset="utf-8">
<title>Inventories – Inventory Drivers</title>
<link href="https://fonts.googleapis.com/css2?family=Jost:wght@500;600;700&display=swap" rel="stylesheet">
<style>
  :root {
    --navy: #1b3a87;
    --cyan: #0cb1f0;
    --orange: #f7941d;
    --white: #ffffff;
    --frame: #d6d6d6;
  }
  html, body {
    margin: 0;
    padding: 0;
    overflow: hidden;
    background: var(--white);
  }
  .canvas {
    width: 1200px;
    height: 886px;
    box-sizing: border-box;
    border: 7px solid var(--frame);
    background: var(--white);
    font-family: "Jost", "Futura", sans-serif;
  }
  .diagram { display: block; }
  .connector { stroke: var(--navy); stroke-width: 2.2; fill: none; }
  .pill { fill: var(--cyan); }
  .page-title { fill: var(--navy); font-size: 39px; font-weight: 600; }
  .column-head { fill: var(--navy); font-size: 21px; font-weight: 600; text-anchor: middle; }
  .hub-ring { fill: var(--white); stroke: var(--navy); stroke-width: 2.5; }
  .hub-core { fill: var(--cyan); }
  .hub-label { fill: var(--white); font-size: 31px; font-weight: 600; text-anchor: middle; letter-spacing: 0.5px; }
  .step-badge { fill: var(--white); stroke: var(--orange); stroke-width: 2.5; }
  .step-number { fill: var(--navy); font-size: 28px; font-weight: 600; text-anchor: middle; }
  .group-label { fill: var(--white); font-size: 20px; font-weight: 600; }
  .sub-label { fill: var(--white); font-size: 14.5px; font-weight: 600; text-anchor: middle; }
</style>
</head>
<body>
<div class="canvas">
<svg class="diagram" width="1186" height="872" viewBox="7 7 1186 872" xmlns="http://www.w3.org/2000/svg">
  <text class="page-title" x="89" y="124">INVENTORIES</text>
  <text class="column-head" x="554" y="127">DRIVER GROUP</text>
  <text class="column-head" x="942" y="127">SUB-GROUP</text>

  <!-- trunk -->
  <path class="connector" d="M346 492 H396 M396 244 V726 M396 244 H424 M396 421 H424 M396 569 H424 M396 726 H424"/>

  <!-- hub -->
  <circle class="hub-ring" cx="219" cy="492" r="128"/>
  <circle class="hub-core" cx="219" cy="492" r="116"/>
  <text class="hub-label" x="219" y="484">INVENTORY</text>
  <text class="hub-label" x="219" y="518">DRIVERS</text>

  <!-- branches -->
  <path class="connector" d="M686 244 H744 M744 167 V318 M744 167 H778 M744 217 H778 M744 268 H778 M744 318 H778"/>
  <path class="connector" d="M686 421 H778 M744 372 V471 M744 372 H778 M744 471 H778"/>
  <path class="connector" d="M686 569 H778 M744 524 V616 M744 524 H778 M744 616 H778"/>
  <path class="connector" d="M686 726 H778 M744 675 V778 M744 675 H778"/>

  <!-- driver groups -->
  <g class="driver-group">
    <path class="pill" d="M480 222 H664 a21.5 21.5 0 0 1 0 43 H480 q6 -21.5 0 -43 Z"/>
    <circle class="step-badge" cx="451" cy="244" r="27"/>
    <text class="step-number" x="451" y="254">10</text>
    <text class="group-label" x="508" y="251">PLANNING</text>
  </g>
  <g class="driver-group">
    <path class="pill" d="M480 400 H664 a21.5 21.5 0 0 1 0 43 H480 q6 -21.5 0 -43 Z"/>
    <circle class="step-badge" cx="451" cy="421" r="27"/>
    <text class="step-number" x="451" y="431">11</text>
    <text class="group-label" x="508" y="428">PROCUREMENT</text>
  </g>
  <g class="driver-group">
    <path class="pill" d="M480 548 H664 a21.5 21.5 0 0 1 0 43 H480 q6 -21.5 0 -43 Z"/>
    <circle class="step-badge" cx="451" cy="569" r="27"/>
    <text class="step-number" x="451" y="579">12</text>
    <text class="group-label" x="508" y="576">FULFILMENT</text>
  </g>
  <g class="driver-group">
    <path class="pill" d="M480 705 H664 a21.5 21.5 0 0 1 0 43 H480 q6 -21.5 0 -43 Z"/>
    <circle class="step-badge" cx="451" cy="726" r="27"/>
    <text class="step-number" x="451" y="736">13</text>
    <text class="group-label" x="508" y="733">PRODUCT RANGE</text>
  </g>

  <!-- sub-groups -->
  <g class="sub-group">
    <rect class="pill" x="777" y="151.5" width="332" height="31" rx="15.5"/><text class="sub-label" x="942" y="172">DEMAND VARIABILITY</text>
    <rect class="pill" x="777" y="201.5" width="332" height="31" rx="15.5"/><text class="sub-label" x="937" y="222">PLANNING COLLABORATION</text>
    <rect class="pill" x="777" y="252.5" width="332" height="31" rx="15.5"/><text class="sub-label" x="942" y="273">INFORMATION AVAILABILITY</text>
    <rect class="pill" x="777" y="302.5" width="332" height="31" rx="15.5"/><text class="sub-label" x="942" y="323">INVENTROY TARGET SETTING</text>

    <rect class="pill" x="777" y="356.5" width="332" height="31" rx="15.5"/><text class="sub-label" x="942" y="377">ORDER QUANTITIES</text>
    <rect class="pill" x="777" y="407.5" width="332" height="31" rx="15.5"/><text class="sub-label" x="942" y="428">SUPPLIER LEAD TIME VARIABILITY</text>
    <rect class="pill" x="777" y="455.5" width="332" height="31" rx="15.5"/><text class="sub-label" x="942" y="476">SUPPLIER QUALITY VARIABILITY</text>

    <rect class="pill" x="777" y="508.5" width="332" height="31" rx="15.5"/><text class="sub-label" x="942" y="529">CUSTOMER SERVICE LEVELS</text>
    <rect class="pill" x="777" y="553.5" width="332" height="31" rx="15.5"/><text class="sub-label" x="942" y="574">NETWORK STRUCTURE</text>
    <rect class="pill" x="777" y="600.5" width="332" height="31" rx="15.5"/><text class="sub-label" x="942" y="621">INVENTORY POSTPONEMENT</text>

    <rect class="pill" x="777" y="659.5" width="332" height="31" rx="15.5"/><text class="sub-label" x="942" y="680">CUSTOMER INVENTORY NEEDS</text>
    <rect class="pill" x="777" y="710.5" width="332" height="31" rx="15.5"/><text class="sub-label" x="942" y="731">PART STANDARDISATION</text>
    <rect class="pill" x="777" y="762.5" width="332" height="31" rx="15.5"/><text class="sub-label" x="942" y="783">SKU PROLIFERATION</text>
  </g>
</svg>
</div>
</body>
</html>
```